Business Card for Dental Office - "online review card"

I would like to develop a tasteful card (that would compliment my existing business card) that provides my patients a written link to a portal on my website that would facilitate the generation of online reviews.

My existing business card was a Lumaquarry project a few years ago and has been well received. I hope that it is easily accessed online for reference.

Target Market(s)

Existing patients who need guidance in accessing the "write a review" section of my website

Industry/Entity Type

Business

Requirements
Must have
• -a similar look to my existing card:
http://www.lumaquarry.com.au/contest.aspx?id=5192&page=3

-a link to the following url in writing:
http://www.tessaroldental.com/reviews.html

- a reference to "appreciating feedback" or "how are we doing?"

```html
<!DOCTYPE html>
<html lang="en">
<head>
<meta charset="utf-8">
<title>Tessarol Dental – Review Card</title>
<link rel="stylesheet" href="https://fonts.googleapis.com/css2?family=Montserrat:wght@400&family=Open+Sans:wght@400;700&display=swap">
<style>
  :root {
    --backdrop: #e4e4e4;
    --card: #ffffff;
    --card-edge: #9a9a9a;
    --brand-blue: #33318a;
    --brand-deep: #26246b;
    --brand-light: #6b66bf;
    --name-grey: #5a5a5a;
    --white: #ffffff;
  }
  * { margin: 0; padding: 0; box-sizing: border-box; }
  html, body { width: 1200px; height: 711px; overflow: hidden; background: var(--backdrop); }
  .stage { position: relative; width: 1200px; height: 711px; }
  .card {
    position: absolute; width: 514px; height: 293px;
    background: var(--card); border: 1px solid var(--card-edge);
    border-radius: 9px; overflow: hidden;
  }
  .card--review { left: 65px; top: 39px; }
  .card--back { left: 627px; top: 39px; }
  .card--mark { left: 346px; top: 369px; }

  .wave { position: absolute; inset: 0; width: 100%; height: 100%; }

  .brand-square {
    position: absolute; background: var(--brand-blue); border-radius: 12px;
  }
  .brand-name {
    position: absolute; font-family: "Montserrat", sans-serif; font-weight: 400;
    color: var(--name-grey); white-space: nowrap; letter-spacing: -0.3px;
  }
  .brand-sub {
    position: absolute; font-family: "Montserrat", sans-serif; font-weight: 400;
    color: var(--name-grey); white-space: nowrap; text-transform: uppercase;
  }

  .card--review .brand-square { left: 45px; top: 30px; width: 78px; height: 78px; }
  .card--review .brand-name { left: 146px; top: 34px; font-size: 24px; }
  .card--review .brand-sub { right: 84px; top: 66px; font-size: 9px; letter-spacing: 2.6px; }

  .review-label {
    position: absolute; left: 32px; top: 210px;
    font-family: "Open Sans", sans-serif; font-weight: 400; font-size: 16px;
    color: var(--white); text-transform: uppercase;
  }
  .review-link {
    position: absolute; left: 32px; top: 253px;
    font-family: "Open Sans", sans-serif; font-weight: 700; font-size: 18px;
    color: var(--white); white-space: nowrap;
  }

  .card--back .brand-square { left: 37px; top: 97px; width: 90px; height: 90px; }
  .card--back .brand-name { left: 155px; top: 103px; font-size: 28px; }
  .card--back .brand-sub { right: 30px; top: 138px; font-size: 11px; letter-spacing: 3px; }

  .card--mark .brand-square { left: 171px; top: 38px; width: 175px; height: 175px; border-radius: 22px; }
  .card--mark .brand-name { left: 0; right: 0; top: 228px; text-align: center; font-size: 18px; }
  .card--mark .brand-sub { left: 0; right: 0; top: 252px; text-align: center; font-size: 7px; letter-spacing: 1.8px; }
</style>
</head>
<body>
<main class="stage">
  <section class="card card--review">
    <svg class="wave" viewBox="0 0 514 293" preserveAspectRatio="none" aria-hidden="true">
      <path d="M0,70 C130,92 230,122 330,177 C400,217 460,222 514,200 L514,293 L0,293 Z" fill="var(--brand-blue)"/>
      <path d="M0,70 C130,92 230,122 330,177 C400,217 460,222 514,200 L514,214 C460,236 400,232 330,192 C230,137 130,105 0,86 Z" fill="var(--brand-light)"/>
      <path d="M0,90 C130,108 230,139 330,196 C400,236 460,240 514,220" fill="none" stroke="var(--white)" stroke-width="4"/>
      <path d="M0,100 C130,118 240,152 340,208 C410,245 465,245 514,230" fill="none" stroke="var(--white)" stroke-width="1.5"/>
      <rect x="33" y="18" width="102" height="102" rx="14" fill="var(--white)"/>
    </svg>
    <div class="brand-square"></div>
    <div class="brand-name">Marcus J. Tessarol, DDS</div>
    <div class="brand-sub">and Associates</div>
    <div class="review-label">Appreciating Feedback</div>
    <div class="review-link">http://www.tessaroldental.com/reviews.html</div>
  </section>

  <section class="card card--back">
    <div class="brand-square"></div>
    <div class="brand-name">Marcus J. Tessarol, DDS</div>
    <div class="brand-sub">and Associates</div>
  </section>

  <section class="card card--mark">
    <div class="brand-square"></div>
    <div class="brand-name">Marcus J. Tessarol, DDS</div>
    <div class="brand-sub">Family and Cosmetic Dentistry</div>
  </section>
</main>
</body>
</html>
```